Wine Label Redesign For California Wine Company

We’re looking to refresh our brand with a new professional looking label. We love what we have and was well received over the past three years and would like to keep a couple of the element: Name (Mark Dunlow), it doesn’t have to be in cursive. The swirl, this how everybody recognizes our brand as it’s also in our logo. Colors: Gold and whatever you think is awesome. Looking forward to seeing your work.

Target Market(s)

Retailers

Industry/Entity Type

Winery

Font styles to use
Serif
Script

Colors

Designer to choose colors to be used in the design.

Requirements
Must have
• Front Label:
• Nocturne (Varietal)
• 2016 (vintage)
• Lodi, California (location)
• Mark Dunlow (Name)
• Back Label:
• Government Warning
• www.dunlowvinco.com (website)
• 2016 (vintage)
• Swirl
Nice to have
• Creativity
• Bold colors
• Something that pops
Should not have
• Should not look nothing like my old label.

```html
<!DOCTYPE html>
<html lang="en">
<head>
<meta charset="utf-8">
<title>Nocturne – Mark Dunlow Wine Labels</title>
<link href="https://fonts.googleapis.com/css2?family=Cinzel:wght@400&family=Cormorant+Garamond:wght@500;700&family=Merriweather:wght@700&display=swap" rel="stylesheet">
<style>
  :root {
    --backdrop: #c1b9b3;
    --ink: #050505;
    --gold: #c9a545;
    --gold-light: #e6cf7a;
    --cream: #f7f1e4;
    --cream-deep: #dccfb6;
    --text-dark: #1a1a1a;
    --white: #f2f2f2;
  }
  * { box-sizing: border-box; margin: 0; padding: 0; }
  html, body { width: 986px; height: 1200px; overflow: hidden; }
  body { background: var(--backdrop); position: relative; font-variant-numeric: lining-nums; }

  .label {
    position: absolute; top: 718px; width: 410px; height: 411px;
    background: var(--ink); overflow: hidden;
  }
  .label--front { left: 68px; }
  .label--back { left: 508px; }

  .varietal {
    position: absolute; top: 0; left: 0; right: 0; height: 62px;
    display: flex; align-items: center; justify-content: center;
    font-family: "Cinzel", serif; font-weight: 400; font-size: 27px; letter-spacing: 8px;
    color: var(--gold); padding-left: 8px;
  }
  .panel {
    position: absolute; top: 62px; left: 0; right: 0; height: 264px;
    border-top: 2px solid var(--gold); border-bottom: 2px solid var(--gold);
  }
  .panel__pattern {
    position: absolute; inset: 3px 0;
    background: linear-gradient(90deg, var(--cream-deep) 0%, var(--cream) 25%, #fffdf8 50%, var(--cream) 75%, var(--cream-deep) 100%);
  }
  .origin {
    position: absolute; top: 340px; left: 0; right: 0; text-align: center;
  }
  .origin__place {
    display: inline-block; padding: 2px 2px;
    border-top: 1px solid var(--gold); border-bottom: 1px solid var(--gold);
    font-family: "Merriweather", serif; font-size: 17px; letter-spacing: 2.5px;
    color: var(--gold-light);
  }
  .origin__vintage {
    margin-top: 7px; font-family: "Cinzel", serif; font-size: 11px;
    letter-spacing: 7px; color: var(--white); padding-left: 7px;
  }

  /* front */
  .producer-vertical {
    position: absolute; left: 112px; top: 134px;
    transform: translate(-50%, -50%) rotate(-90deg);
    white-space: nowrap;
    font-family: "Cormorant Garamond", serif; font-weight: 700; font-size: 40px;
    color: var(--text-dark);
  }
  .mark-dot {
    position: absolute; left: 186px; top: 85px; width: 100px; height: 100px;
    border-radius: 50%; background: var(--gold);
  }

  /* back */
  .producer-row {
    position: absolute; top: 42px; left: 0; right: 0;
    display: flex; align-items: center; justify-content: center; gap: 12px;
  }
  .producer-row__name {
    font-family: "Cormorant Garamond", serif; font-weight: 700; font-size: 30px;
    color: var(--text-dark);
  }
  .producer-row__dot {
    width: 32px; height: 32px; border-radius: 50%; background: var(--gold);
  }
  .warning {
    position: absolute; top: 102px; left: 58px; right: 56px;
    font-family: "Cormorant Garamond", serif; font-weight: 500; font-size: 10.5px;
    line-height: 12.5px; text-transform: uppercase; text-align: justify;
    color: var(--text-dark);
  }
  .warning strong { font-weight: 700; }
  .facts {
    position: absolute; top: 194px; left: 56px; right: 56px;
    border: 1px solid var(--ink);
  }
  .facts__row {
    height: 24px; display: flex; align-items: center; justify-content: center; gap: 6px;
    font-family: "Cormorant Garamond", serif; font-weight: 700; font-size: 10.5px;
    color: var(--text-dark); background: rgba(255,255,255,0.4);
  }
  .facts__web {
    height: 26px; background: var(--ink); display: flex; align-items: center; justify-content: center;
    font-family: "Cinzel", serif; font-size: 10px; letter-spacing: 2.5px; color: var(--gold);
  }
</style>
</head>
<body>
  <section class="label label--front">
    <h1 class="varietal">Nocturne</h1>
    <div class="panel">
      <div class="panel__pattern" role="img" aria-label="Cream damask ornamental pattern background"></div>
      <p class="producer-vertical">Mark Dunlow</p>
      <div class="mark-dot"></div>
    </div>
    <div class="origin">
      <span class="origin__place">Lodi, California</span>
      <p class="origin__vintage">2016</p>
    </div>
  </section>

  <section class="label label--back">
    <h2 class="varietal">Nocturne</h2>
    <div class="panel">
      <div class="panel__pattern" role="img" aria-label="Cream damask ornamental pattern background"></div>
      <div class="producer-row">
        <span class="producer-row__name">Mark Dunlow</span>
        <span class="producer-row__dot"></span>
      </div>
      <p class="warning"><strong>Government Warning:</strong> (1) According to the Surgeon General, women should not drink alcoholic beverages during pregnancy because of the risk of birth defects. (2) Consumption of alcoholic beverages impairs your ability to drive a car or operate machinery, and may cause health problems.</p>
      <div class="facts">
        <div class="facts__row"><span>CONTAINS SULFITES</span><span>|</span><span>ALC 14.2% BY VOL</span><span>|</span><span>750ML</span></div>
        <div class="facts__web">WWW.DUNLOWVINCO.COM</div>
      </div>
    </div>
    <div class="origin">
      <span class="origin__place">Lodi, California</span>
      <p class="origin__vintage">2016</p>
    </div>
  </section>
</body>
</html>
```